The design should look similar to the uploaded example to accommodate the information needed for a business card template. I would like to see the colors orange and charcoal grey incorporated along with the logo.The following should be on the back of the card SPECIALIZING IN NEW AND USED TIRES & WHEELS FOR:- Loaders- Skid Steers- Telehandlers- Boom Lifts- Forklifs and moreELIMINATING DOWNTIMEWheel Exchange Program for New & Used Foam Filled and Solid Rubber TiresSPECIALTY SERVICES- Foam Filling Tires- Largest Tire Press in SE- ONSITE Forklift Tire Press- Boom Truck Services - Rubber Tracks

Target Market(s)

New and Existing Customers

Industry/Entity Type

Business

Contact Information for Business Card

NAMEHEAVY DUTY TIRE, LLC8470 Belvedere RoadWest Palm Beach, FL 33411P: 844-HD-TIRESF: 561-431-6469C:E: W: WWW.GRANITERIMSUPPLY-EXAMPLE.COM

Font styles to use
Sans Serif

Colors
f37122
333333

Requirements
Must have
• The logo and the information indicated for the backside of the card
Nice to have
• Keep the orange and charcoal grey colors

```html
<!DOCTYPE html>
<html lang="en">
<head>
<meta charset="utf-8">
<title>Granite Rim Supply LLC – Business Card</title>
<link rel="stylesheet" href="https://fonts.googleapis.com/css2?family=Rye&family=PT+Sans:wght@400;700&family=Tinos:wght@400;700&display=swap">
<style>
  :root {
    --backdrop: #1e2022;
    --orange: #f58840;
    --charcoal: #353b3b;
    --white: #ffffff;
    --phone-purple: #4a3aa6;
    --ink: #2a2a2a;
    --faint-mark: #d9d4cf;
  }
  * { margin: 0; padding: 0; box-sizing: border-box; }
  html, body { width: 1200px; height: 800px; overflow: hidden; }
  body { background: var(--backdrop); position: relative; }

  .card {
    position: absolute;
    left: 372px;
    width: 456px;
    height: 282px;
    overflow: hidden;
    box-shadow: 0 6px 18px rgba(0,0,0,0.45);
  }
  .card-front { top: 118px; background: var(--orange); }
  .card-back { top: 418px; background: var(--white); }
  .card-shapes { position: absolute; inset: 0; width: 456px; height: 282px; }

  .company-title {
    position: absolute; right: 43px; top: 30px;
    font-family: "Rye", serif; font-size: 25px; color: var(--charcoal);
    letter-spacing: 0.5px; white-space: nowrap;
  }
  .contact {
    position: absolute; right: 43px; top: 96px; text-align: right;
    font-family: "PT Sans", sans-serif; color: var(--white);
  }
  .contact p { font-size: 18px; line-height: 19px; }
  .contact .phone { color: var(--phone-purple); font-size: 23px; line-height: 27px; margin-top: 3px; }
  .contact .fax { font-size: 20px; line-height: 23px; }
  .contact .web { font-size: 18px; line-height: 22px; }

  .brand-mark {
    position: absolute; left: 30px; top: 109px; width: 114px; height: 114px;
    border-radius: 50%; background: var(--charcoal);
    display: flex; align-items: center; justify-content: center; text-align: center;
    font-family: "PT Sans", sans-serif; font-weight: 700; font-size: 15px; line-height: 17px;
    color: var(--white);
  }

  .back-text { position: absolute; font-family: "Tinos", serif; color: var(--ink); font-size: 11.5px; }
  .specialty-intro { left: 40px; top: 86px; }
  .specialty-intro h2 { font-size: 11.5px; font-weight: 700; line-height: 14px; margin-bottom: 5px; }
  .specialty-intro li { list-style: none; line-height: 17.5px; }
  .services { right: 37px; top: 86px; text-align: right; }
  .services h2 { font-size: 11.5px; font-weight: 700; line-height: 14px; margin-bottom: 5px; }
  .services li { list-style: none; line-height: 17px; }
</style>
</head>
<body>

<section class="card card-front">
  <svg class="card-shapes" viewBox="0 0 456 282" aria-hidden="true">
    <polygon points="0,231 146,213 456,282 0,282" fill="var(--charcoal)"/>
    <polygon points="0,245 146,228 410,282 0,282" fill="var(--white)"/>
  </svg>
  <div class="brand-mark">GRANITE<br>RIM<br>SUPPLY</div>
  <h1 class="company-title">GRANITE RIM SUPPLY LLC</h1>
  <div class="contact">
    <p>5126 Marston Lane</p>
    <p>West Palm Beach, FL 33411</p>
    <p class="phone">P: 844-GR-WHEEL</p>
    <p class="fax">F: 561-278-9053</p>
    <p class="web">www.graniterimsupply-example.com</p>
  </div>
</section>

<section class="card card-back">
  <svg class="card-shapes" viewBox="0 0 456 282" aria-hidden="true">
    <polygon points="140,0 456,0 456,282 292,282" fill="var(--orange)"/>
    <circle cx="265" cy="255" r="56" fill="var(--faint-mark)" opacity="0.55"/>
  </svg>
  <div class="back-text specialty-intro">
    <h2>specializing in new and<br>used tires &amp; wheels for:</h2>
    <ul>
      <li>Loaders</li>
      <li>Skid Steers</li>
      <li>Telehandlers</li>
      <li>Boom Lifts</li>
      <li>Forklifs and more</li>
    </ul>
  </div>
  <div class="back-text services">
    <h2>Wheel Exchange Program for New &amp;<br>Used Foam Filled and Solid Rubber Tires</h2>
    <ul>
      <li>SPECIALTY SERVICES</li>
      <li>Foam Filling Tires</li>
      <li>Largest Tire Press in SE</li>
      <li>ONSITE Forklift Tire Press</li>
      <li>Boom Truck Services</li>
      <li>Rubber Tracks</li>
    </ul>
  </div>
</section>

</body>
</html>
```